Residential & commercial landscaping company

Updated business cards for commercial and landscaping company. We would like to keep out logo, but just need a more updated business card.

```html
<!DOCTYPE html>
<html lang="en">
<head>
<meta charset="utf-8">
<title>GreenTerra Business Cards</title>
<link rel="stylesheet" href="https://fonts.googleapis.com/css2?family=Arimo:wght@400;700&family=Libre+Baskerville:wght@700&display=swap">
<style>
  :root {
    --backdrop: #1f1f1f;
    --green-light: #5cc85a;
    --green-mid: #0a9a34;
    --green-deep: #0b6e36;
    --accent: #2fbf2f;
    --ink: #111111;
    --paper: #ffffff;
  }
  * { margin: 0; padding: 0; box-sizing: border-box; }
  html, body {
    width: 1200px; height: 900px; overflow: hidden;
    background: var(--backdrop);
  }
  .canvas { position: relative; width: 1200px; height: 900px; }
  .card {
    position: absolute; left: 250px; width: 700px; height: 400px;
    overflow: hidden;
    box-shadow: 0 10px 30px rgba(0,0,0,.6);
  }
  .card--front {
    top: 40px;
    background: linear-gradient(160deg, var(--green-light) 0%, var(--green-mid) 55%, var(--green-deep) 100%);
    display: flex; align-items: center; justify-content: center; gap: 18px;
  }
  .brand-mark { width: 34px; height: 34px; background: var(--paper); flex: none; }
  .brand-name {
    font-family: "Arimo", sans-serif; font-weight: 700;
    font-size: 78px; color: var(--paper); letter-spacing: -1px;
    white-space: nowrap;
  }
  .card--back { top: 460px; background: var(--paper); }
  .back-brand {
    position: absolute; left: 130px; top: 30px; width: 110px; height: 340px;
    display: flex; flex-direction: column; align-items: center; justify-content: center; gap: 14px;
  }
  .back-brand .brand-name {
    color: var(--ink); font-size: 60px;
    writing-mode: vertical-rl; transform: rotate(180deg);
  }
  .back-brand .brand-mark { background: var(--green-deep); width: 26px; height: 26px; }
  .contact-block {
    position: absolute; left: 290px; top: 110px; right: 30px;
    font-family: "Arimo", sans-serif; color: var(--ink);
  }
  .person-name {
    font-family: "Libre Baskerville", serif; font-weight: 700;
    font-size: 32px; color: var(--accent); line-height: 1.1;
  }
  .person-title { font-size: 20px; margin-top: 4px; }
  .contact-list { list-style: none; margin-top: 30px; }
  .contact-list li {
    display: flex; align-items: center; gap: 12px;
    font-size: 20px; line-height: 1.5; white-space: nowrap;
  }
  .contact-list svg { width: 20px; height: 20px; fill: var(--accent); flex: none; }
</style>
</head>
<body>
<main class="canvas">
  <section class="card card--front">
    <span class="brand-name">GreenTerra</span>
    <span class="brand-mark"></span>
  </section>

  <section class="card card--back">
    <div class="back-brand">
      <span class="brand-mark"></span>
      <span class="brand-name">GreenTerra</span>
    </div>
    <div class="contact-block">
      <h1 class="person-name">Daniel Harlow Jr.</h1>
      <p class="person-title">Project Manager</p>
      <ul class="contact-list">
        <li>
          <svg viewBox="0 0 24 24" aria-hidden="true"><path d="M6.6 10.8a15.1 15.1 0 0 0 6.6 6.6l2.2-2.2c.3-.3.7-.4 1-.2 1.1.4 2.3.6 3.6.6.6 0 1 .4 1 1V20c0 .6-.4 1-1 1A17 17 0 0 1 3 4c0-.6.4-1 1-1h3.5c.6 0 1 .4 1 1 0 1.3.2 2.5.6 3.6.1.3 0 .7-.2 1z"/></svg>
          555-204-7316 ext.214
        </li>
        <li>
          <svg viewBox="0 0 24 24" aria-hidden="true"><path d="M7 3h10v5H7zM4 9h16a2 2 0 0 1 2 2v6h-4v4H6v-4H2v-6a2 2 0 0 1 2-2zm4 7v3h8v-3z"/></svg>
          555-380-4928
        </li>
        <li>
          <svg viewBox="0 0 24 24" aria-hidden="true"><path d="M2 5h20v14H2zm2 2v.5l8 5 8-5V7l-8 5z"/></svg>
          dan@GreenTerraLandscapes.com
        </li>
      </ul>
    </div>
  </section>
</main>
</body>
</html>
```